Young, modern, highly skilled carpenter needs business card design

I need a business card design for my construction business. Its called 'Barlow Construction Services'. Im looking for a ultra modern design that incorporates B C S, the first letters of the name with only a subtle reference to carpentry. The design should reflect my high quality work and eye for detail. i have also uploaded some exmaple designs i like.

Industry/Entity Type

Construction

Requirements
Must have
• Name of business, my name, mobile number, ABN number, email address
Nice to have
• A logo incorporating the name of the business

```html
<!DOCTYPE html>
<html lang="en">
<head>
<meta charset="utf-8">
<title>Barlow Construction Services – Business Card</title>
<link rel="stylesheet" href="https://fonts.googleapis.com/css2?family=Open+Sans:wght@400;700&display=swap">
<style>
  :root {
    --backdrop: #7d8c8c;
    --card-white: #ffffff;
    --brand-green: #55ff00;
    --ink: #111111;
    --paper-text: #ffffff;
  }
  * { margin: 0; padding: 0; box-sizing: border-box; }
  html, body {
    width: 1200px;
    height: 900px;
    overflow: hidden;
  }
  body {
    background: var(--backdrop);
    font-family: "Open Sans", sans-serif;
    position: relative;
  }
  .card {
    position: absolute;
  }
  .card--front {
    left: 335px;
    top: 60px;
    width: 538px;
    height: 370px;
    background: var(--card-white);
    display: flex;
    align-items: center;
    justify-content: center;
  }
  .card--back {
    left: 334px;
    top: 459px;
    width: 547px;
    height: 376px;
    background: var(--brand-green);
  }
  .wordmark {
    display: flex;
    align-items: center;
    gap: 10px;
    font-weight: 700;
    color: var(--ink);
    letter-spacing: 2px;
    line-height: 1;
  }
  .wordmark__square {
    display: block;
    background: var(--brand-green);
  }
  .wordmark--front {
    font-size: 60px;
    margin-top: -16px;
  }
  .wordmark--front .wordmark__square {
    width: 18px;
    height: 18px;
  }
  .wordmark--back {
    position: absolute;
    right: 68px;
    top: 252px;
    font-size: 44px;
  }
  .wordmark--back .wordmark__square {
    width: 14px;
    height: 14px;
    background: var(--paper-text);
  }
  .contact {
    position: absolute;
    left: 69px;
    top: 52px;
    color: var(--paper-text);
    font-size: 18.5px;
    line-height: 26px;
  }
  .contact__name {
    color: var(--ink);
    font-weight: 700;
    font-size: 20px;
    margin-bottom: 2px;
  }
  .contact__divider {
    color: var(--ink);
  }
  .business-name {
    position: absolute;
    left: 67px;
    top: 298px;
    color: var(--paper-text);
    font-weight: 700;
    font-size: 20.5px;
    text-transform: uppercase;
    letter-spacing: 0.1px;
  }
</style>
</head>
<body>
  <section class="card card--front" aria-label="Card front">
    <div class="wordmark wordmark--front">
      <span class="wordmark__square"></span>
      <span class="wordmark__text">BCS</span>
    </div>
  </section>

  <section class="card card--back" aria-label="Card back">
    <div class="contact">
      <p class="contact__name">Nathan Barlow</p>
      <p class="contact__email">nathan_barlow@mailbox.com</p>
      <p class="contact__phone">0412 583206 <span class="contact__divider">//</span> ABN 51 824 753 019</p>
    </div>
    <div class="wordmark wordmark--back">
      <span class="wordmark__square"></span>
      <span class="wordmark__text">BCS</span>
    </div>
    <p class="business-name">Barlow Construction Services</p>
  </section>
</body>
</html>
```